Stylish Business Cards Wanted

- DOUBLE SIDED Design Required -

High end, edgy cards for a corporate and personal stylist. Must include logo,
Name: Belinda Harwick
Title: Director and Stylist
telephone : +61 8 7142 5809
email: belinda@theloombriefing.example
website: theloombriefing.example
Tag: Corporate Workwear & Uniform Specialist | Personal Stylist
Would like nice icons for telephone, email, website

Target Market(s)

Businesses wanting stylish uniforms, people wanting stylish wardrobes

Industry/Entity Type

Corporate Workwear Stylist

Contact Information for Business Card

I would like black, white and gold foiling incorporated in the design - possibly a touch of the other colours on my branding guide attached Name: Belinda Harwick Title: Director and Stylist telephone : +61 8 7142 5809 email: belinda@theloombriefing.example website: theloombriefing.example Tag: Corporate Workwear & Uniform Specialist | Personal Stylist Would like nice icons for telephone, email, website

Font styles to use
Other font styles liked:
• Raleway

Colors

Designer to choose colors to be used in the design.

Requirements
Must have
• Gold foil accents

```html
<!DOCTYPE html>
<html lang="en">
<head>
<meta charset="utf-8">
<title>The Loom Briefing – Business Cards</title>
<link href="https://fonts.googleapis.com/css2?family=Raleway:wght@700&family=Roboto:wght@400&family=Dancing+Script:wght@600&display=swap" rel="stylesheet">
<style>
  :root {
    --backdrop: #3a3b3e;
    --card-black: #26262b;
    --gold: #d9a93a;
    --gold-panel: #ebb756;
    --navy: #1e2140;
    --pink: #e0157a;
    --pink-dark: #a70f5a;
    --white: #ffffff;
  }
  html, body {
    margin: 0;
    padding: 0;
    width: 799px;
    height: 1200px;
    overflow: hidden;
    background: var(--backdrop);
  }
  .sheet {
    position: relative;
    width: 799px;
    height: 1200px;
  }
  .card {
    position: absolute;
    left: 80px;
    width: 640px;
    height: 366px;
    border-radius: 24px;
    overflow: hidden;
    background: var(--card-black);
    box-shadow: 0 18px 40px rgba(0,0,0,0.35);
  }
  .card--front { top: 130px; }
  .card--back { top: 700px; }

  .brand-name {
    font-family: "Raleway", sans-serif;
    font-weight: 700;
    text-transform: uppercase;
    text-align: center;
    margin: 0;
  }
  .card--front .brand-name {
    position: absolute;
    inset: 0;
    display: flex;
    flex-direction: column;
    justify-content: center;
    color: var(--gold);
    font-size: 46px;
    letter-spacing: 6px;
    line-height: 1.15;
  }

  .back-art { position: absolute; inset: 0; }
  .card--back .brand-name {
    position: absolute;
    left: 20px;
    top: 92px;
    width: 200px;
    color: var(--navy);
    font-size: 25px;
    letter-spacing: 3px;
    line-height: 1.2;
  }
  .tagline {
    position: absolute;
    left: 196px;
    top: 262px;
    width: 430px;
    height: 38px;
    margin: 0;
    line-height: 38px;
    font-family: "Dancing Script", cursive;
    font-weight: 600;
    font-size: 16px;
    color: var(--white);
    white-space: nowrap;
  }
  .tagline .divider { margin: 0 8px; }

  .contact {
    position: absolute;
    left: 300px;
    top: 70px;
    color: var(--white);
    font-family: "Roboto", sans-serif;
  }
  .contact__name {
    font-family: "Dancing Script", cursive;
    font-weight: 600;
    font-size: 31px;
    color: var(--gold);
    margin: 0;
    line-height: 1.1;
  }
  .contact__title {
    font-size: 14px;
    margin: 2px 0 18px;
  }
  .contact__list {
    list-style: none;
    margin: 0;
    padding: 0;
  }
  .contact__item {
    display: flex;
    align-items: center;
    gap: 12px;
    font-size: 15.5px;
    height: 27px;
  }
  .contact__icon { width: 16px; height: 16px; flex: none; }
</style>
</head>
<body>
<main class="sheet">

  <section class="card card--front" aria-label="Business card front">
    <h1 class="brand-name"><span>The Loom</span><span>Briefing</span></h1>
  </section>

  <section class="card card--back" aria-label="Business card back">
    <svg class="back-art" viewBox="0 0 640 366" width="640" height="366" aria-hidden="true">
      <path d="M0 0 H215 C268 90 262 200 196 262 L176 366 H0 Z" fill="var(--gold-panel)"/>
      <path d="M215 0 C268 90 262 200 196 262 L212 262 C282 196 284 88 224 0 Z" fill="var(--pink)"/>
      <path d="M166 262 L184 262 L184 300 Z" fill="var(--pink-dark)"/>
      <path d="M176 262 H640 V300 H166 Z" fill="var(--pink)"/>
    </svg>

    <p class="brand-name">The Loom<br>Briefing</p>

    <div class="contact">
      <h2 class="contact__name">Belinda Harwick</h2>
      <p class="contact__title">Director and Stylist</p>
      <ul class="contact__list">
        <li class="contact__item">
          <svg class="contact__icon" viewBox="0 0 16 16" aria-hidden="true">
            <circle cx="8" cy="8" r="7" fill="none" stroke="var(--gold)" stroke-width="1.3"/>
            <path d="M5.6 4.6 L6.8 6 L6.2 7 Q7 8.8 8.9 9.8 L9.9 9.2 L11.3 10.4 L10.5 11.5 Q6.6 11 4.5 5.6 Z" fill="var(--gold)"/>
          </svg>
          +61 8 7142 5809
        </li>
        <li class="contact__item">
          <svg class="contact__icon" viewBox="0 0 16 16" aria-hidden="true">
            <rect x="1.5" y="3.5" width="13" height="9" fill="none" stroke="var(--gold)" stroke-width="1.3"/>
            <path d="M1.5 3.5 L8 9 L14.5 3.5" fill="none" stroke="var(--gold)" stroke-width="1.3"/>
          </svg>
          belinda@theloombriefing.example
        </li>
        <li class="contact__item">
          <svg class="contact__icon" viewBox="0 0 16 16" aria-hidden="true">
            <circle cx="8" cy="8" r="6.5" fill="none" stroke="var(--gold)" stroke-width="1.3"/>
            <ellipse cx="8" cy="8" rx="2.8" ry="6.5" fill="none" stroke="var(--gold)" stroke-width="1.1"/>
            <path d="M1.5 8 H14.5 M2.6 4.8 H13.4 M2.6 11.2 H13.4" stroke="var(--gold)" stroke-width="1.1"/>
          </svg>
          www.theloombriefing.example
        </li>
      </ul>
    </div>

    <p class="tagline">Corporate Workwear &amp; Uniform Specialist<span class="divider">|</span>Personal Stylist</p>
  </section>

</main>
</body>
</html>
```